Business Card Design

Just looking for a good designs that looks good with our company logo. I'd like it to be simple and to the point. Just including contact information, our logo, and my name somewhere on the card so future clients know who they're contacting, and a couple services offered. The two images I attached are pictures of our logo. I don't care which color they they are, I just attached both images to give a reference of logo colors depending on the color of the card.
Names: Carl Whitby
Phone: 816-555-0147
Email: greenstripeyard@fernmail.test
Services offered:
Mowing
Fertilization
Aeration
Bed & tree maintenance
and more.
Business
Names: Carl Whitby
Phone: 816-555-0147
(no website)

```html
<!DOCTYPE html>
<html lang="en">
<head>
<meta charset="utf-8">
<title>Greenstripe Yard Care – Business Card</title>
<link href="https://fonts.googleapis.com/css2?family=Questrial&display=swap" rel="stylesheet">
<style>
  :root {
    --ink: #111111;
    --paper: #ffffff;
    --brand-red: #e4202a;
    --brand-red-dark: #a3121a;
    --brand-navy: #1c2a44;
    --accent-lime: #b9c93a;
    --edge-grey: #e6e6e8;
  }
  * { margin: 0; padding: 0; box-sizing: border-box; }
  html, body {
    width: 1200px;
    height: 695px;
    overflow: hidden;
    background: var(--paper);
  }
  .card {
    position: relative;
    width: 1200px;
    height: 695px;
    background: var(--paper);
    font-family: "Questrial", "Century Gothic", sans-serif;
    color: var(--ink);
  }
  .contact {
    position: absolute;
    left: 105px;
    top: 130px;
    width: 500px;
    text-align: center;
  }
  .contact__name {
    font-size: 50px;
    letter-spacing: 6px;
    line-height: 1;
    font-weight: 400;
  }
  .contact__name .initial { font-size: 58px; font-weight: 700; }
  .contact__phone {
    margin-top: 9px;
    font-size: 32px;
    letter-spacing: 5px;
    font-weight: 700;
    line-height: 1;
  }
  .contact__email {
    margin-top: 8px;
    font-size: 36px;
    line-height: 1;
  }
  .services {
    position: absolute;
    left: 109px;
    top: 340px;
  }
  .services__title {
    display: inline-block;
    font-size: 50px;
    font-weight: 400;
    line-height: 1.05;
    padding-bottom: 3px;
    border-bottom: 3px solid var(--ink);
  }
  .services__list {
    list-style: none;
    margin-top: 12px;
  }
  .services__item {
    position: relative;
    padding-left: 47px;
    font-size: 40px;
    line-height: 43px;
  }
  .services__item::before {
    content: "";
    position: absolute;
    left: 2px;
    top: 12px;
    width: 20px;
    height: 20px;
    border-radius: 50%;
    background: var(--brand-red);
    box-shadow: 0 0 0 2px var(--paper), 0 0 0 4px var(--brand-red);
  }
  .brand {
    position: absolute;
    left: 755px;
    top: 140px;
    display: flex;
    align-items: center;
    gap: 16px;
  }
  .brand__dot {
    width: 36px;
    height: 36px;
    border-radius: 50%;
    background: var(--brand-red);
    flex: none;
  }
  .brand__name {
    font-size: 40px;
    line-height: 1.1;
    color: var(--brand-navy);
    font-weight: 400;
  }
  .edge-band {
    position: absolute;
    right: 0;
    top: 0;
    width: 87px;
    height: 695px;
    background: linear-gradient(180deg,
      var(--paper) 0%,
      var(--edge-grey) 25%,
      var(--brand-red) 50%,
      var(--brand-red-dark) 75%,
      var(--accent-lime) 100%);
  }
</style>
</head>
<body>
  <main class="card">
    <section class="contact">
      <h1 class="contact__name"><span class="initial">C</span>arl <span class="initial">W</span>hitby</h1>
      <p class="contact__phone">816-555-0147</p>
      <p class="contact__email">greenstripeyard@fernmail.test</p>
    </section>

    <section class="services">
      <h2 class="services__title">Services Offered</h2>
      <ul class="services__list">
        <li class="services__item">Mowing</li>
        <li class="services__item">Fertilization</li>
        <li class="services__item">Aeration</li>
        <li class="services__item">Bed &amp; tree maintenance</li>
        <li class="services__item">and more.</li>
      </ul>
    </section>

    <div class="brand">
      <span class="brand__dot"></span>
      <p class="brand__name">Greenstripe<br>Yard Care</p>
    </div>

    <div class="edge-band" role="img" aria-label="Decorative vertical band of red, grey and lime stripes along the right edge"></div>
  </main>
</body>
</html>
```